Professional Engineering Web Design

Project Brief: Website Redesign for Mechanical Design Consultancy
Project Overview
I want to update and improve my current website to create a more professional, modern, and high-credibility online presence for my mechanical design consultancy.

Current site: https://valtorix.design/

The new website must communicate expertise, precision, and trust—matching the standard of top engineering and product design agencies.

Reference Websites (Style + Structure Inspiration)
These represent the quality, cleanliness, and professionalism I want to achieve:

https://plinthwaredesign.com/
https://www.sorvane.com/
https://bramlow-uk.com/
Brand Look
Professional, modern, engineering-focused aesthetic
Clean layouts and strong typography
High-quality imagery conveying precision, innovation, and mechanical expertise
Colour scheme and styling must follow my existing logo (attached in project)
Platform Requirements
The website must be built on WordPress
Should use a clean, flexible theme or modern page builder (Elementor, Gutenberg, Bricks, or similar)
Avoid overly complex custom coding so I can easily edit content later
Final deliverable must allow me to manage and update content without developer assistance
Functionality
Fast-loading, lightweight, and smooth user experience
Clean animations and transitions similar to the reference sites
Fully mobile responsive
Clear navigation and strong visual hierarchy
Contact forms optimised for lead generation
Optional: subtle scroll effects, case study sliders, icon animations, etc.
SEO Aspirations
Developer should recommend and implement a modern SEO strategy
Proper on-page SEO setup (titles, meta, schema, alt tags, heading structure)
Optimised site architecture for ranking and crawling
Aim: Generate leads through improved visibility and keyword targeting
Optional but useful: Google Analytics, Google Search Console setup
User Journeys
(Recommended structure)

The site should be crafted around clear, intuitive journeys for each type of visitor:

Potential new clients
Quickly understand what services I offer
View examples of past work / case studies
See credibility indicators (process, expertise, industries served)
Easily contact me or request a project discussion
Returning clients
Access updated portfolio items
Find contact details or book follow-up work easily
General visitors discovering through SEO
Be guided to core service areas
Understand my value proposition quickly
Be invited to learn more or make contact
The developer should design the structure to support these journeys smoothly.

Maintenance Expectations
Website will be maintained by me, so it should be easy to update using relatively basic WordPress skills
Use modular templates and simple backend structure
Avoid unnecessary plugins
Provide brief handover documentation if required
Hosting Preferences
Site is currently hosted via a family member
Open to discussing moving to a paid, reliable hosting provider if preferable for performance and maintainability
Developer may advise on the best hosting setup for WordPress
Content
Most content can be taken from the existing website
Developer is welcome to suggest improvements to structure, layout, and imagery
Must remain easy for me to edit or add new content later (e.g., new projects)
Deliverables
Fully built WordPress website
Clean, professional, modern design inspired by the reference sites
Mobile-responsive across all devices
SEO-ready structure and optimisations
Transfer of website and admin rights
Any design assets, templates, or documentation used

```html
<!DOCTYPE html>
<html lang="en">
<head>
<meta charset="utf-8">
<title>Valtorix Design — Precision Mechanical Design</title>
<link rel="stylesheet" href="https://fonts.googleapis.com/css2?family=Montserrat:wght@400;500;600;700&display=swap">
<style>
:root{
  --blue:#2f5cf2;
  --blue-dark:#2449cf;
  --ink:#151515;
  --dark:#111214;
  --charcoal:#1d1e21;
  --grey-bg:#e8e8eb;
  --text:#222;
  --muted:#6b6b70;
  --line:#d6d6da;
  --white:#fff;
}
*{box-sizing:border-box;margin:0;padding:0}
html,body{width:1200px;height:5381px;overflow:hidden}
body{font-family:"Montserrat",Arial,sans-serif;color:var(--text);background:var(--white);position:relative}
.section{position:absolute;left:0;width:1200px;overflow:hidden}
.abs{position:absolute}
.tag{position:absolute;background:var(--charcoal);color:#fff;font-size:9px;font-weight:500;letter-spacing:.5px;padding:7px 16px;text-transform:uppercase}
.h2{position:absolute;font-size:32px;font-weight:600;line-height:1.22;color:var(--ink)}
.small{font-size:10.5px;line-height:1.6;color:var(--muted)}
.btn{position:absolute;background:var(--blue);color:#fff;font-size:10px;font-weight:700;letter-spacing:.3px;text-transform:uppercase;display:flex;align-items:center;justify-content:center}
.link{color:var(--blue);font-size:10px;text-decoration:underline;font-weight:500}

/* top bar + nav */
.topbar{top:0;height:30px;background:var(--ink);color:#cfcfd4;font-size:9px}
.topbar .crumbs{left:113px;top:10px;letter-spacing:.4px}
.topbar .follow{left:930px;top:10px;color:#fff}
.social{display:flex;gap:6px;position:absolute}
.social span{width:14px;height:14px;border-radius:50%;border:1px solid var(--blue);display:block}
.nav{top:30px;height:70px;background:#fff;border-bottom:1px solid #eee}
.nav .menu{left:113px;top:28px;display:flex;gap:34px;font-size:11px;font-weight:500}
.brand{position:absolute;left:512px;top:0;width:178px;height:100px;background:var(--blue);display:flex;flex-direction:column;align-items:center;justify-content:center;color:#fff;gap:2px}
.brand .dot{width:30px;height:30px;border-radius:50%;background:#fff}
.brand .name{font-size:22px;font-weight:600;letter-spacing:2px}
.brand .sub{font-size:6px;letter-spacing:.6px}
.nav .loc{left:745px;top:28px;font-size:10px;display:flex;gap:6px;align-items:center}
.nav .phone-ic{left:976px;top:30px;width:36px;height:36px;border-radius:50%;background:var(--ink);display:flex;align-items:center;justify-content:center}
.call{position:absolute;right:0;top:30px;width:170px;height:70px;background:var(--blue);color:#fff;text-align:center;padding-top:20px;font-size:9px}
.call b{display:block;font-size:12px;margin-top:3px}

/* hero */
.hero{top:100px;height:586px;background:linear-gradient(100deg,#5d6068 0%,#9a9ca2 40%,#c8c9cc 70%,#b9babd 100%)}
.hero .photo{inset:0}
.hero .shade{inset:0;background:linear-gradient(90deg,rgba(30,32,38,.75),rgba(30,32,38,.2) 65%,rgba(0,0,0,0))}
.hero .tag{left:113px;top:80px}
.hero h1{position:absolute;left:113px;top:122px;font-size:45px;line-height:1.2;font-weight:600;color:#fff;width:560px}
.hero .rule{left:113px;top:300px;width:250px;height:3px;background:var(--blue)}
.hero p{position:absolute;left:113px;top:318px;width:490px;font-size:12.5px;line-height:1.65;color:#fff}
.hero .btn{left:113px;top:395px;width:215px;height:44px}

/* process */
.process{top:686px;height:648px;background:#fff}
.process .tag{left:113px;top:79px}
.process .h2{left:113px;top:115px;width:480px}
.process .lead{left:113px;top:193px;width:470px}
.process .back{left:88px;top:382px;width:200px;height:190px;background:var(--ink)}
.process .team{left:113px;top:246px;width:462px;height:258px;background:linear-gradient(135deg,#6c7480,#b9bec6 50%,#7b828c)}
.process .cap{left:88px;top:504px;width:441px;height:68px;background:var(--ink);color:#fff;padding:16px 0 0 28px}
.process .cap b{font-size:14px;font-weight:600}
.process .cap b i{color:var(--blue);font-style:normal}
.process .cap span{display:block;font-size:9.5px;color:#bbb;margin-top:6px}
.card{position:absolute;background:#fff;box-shadow:0 6px 24px rgba(0,0,0,.08);padding:26px 26px}
.card .num{font-size:22px;font-weight:700;color:var(--blue)}
.card h3{font-size:14px;font-weight:600;line-height:1.2;margin-top:20px;color:var(--ink)}
.card p{font-size:9.5px;line-height:1.55;color:var(--muted);margin-top:8px}
.card .link{display:block;margin-top:10px}
.process .dots{right:0;top:380px;width:320px;height:270px;background:radial-gradient(circle,rgba(150,150,160,.35) 1.2px,transparent 1.6px) 0 0/9px 9px;-webkit-mask:linear-gradient(135deg,transparent 30%,#000);mask:linear-gradient(135deg,transparent 30%,#000)}
.process .btn{left:591px;top:532px;width:178px;height:40px}

/* about */
.about{top:1334px;height:470px;background:var(--grey-bg)}
.about .tag{left:113px;top:110px}
.about .h2{left:113px;top:148px}
.about .body{left:113px;top:200px;width:470px}
.about .btn{left:113px;top:300px;width:177px;height:40px}
.about .mark{left:711px;top:33px;width:400px;height:400px;border-radius:50%;background:var(--blue);display:flex;align-items:center;justify-content:center;color:#fff;font-size:54px;font-weight:600;letter-spacing:3px}
.ghost{position:absolute;left:-4px;font-size:96px;font-weight:700;white-space:nowrap;color:transparent;-webkit-text-stroke:1px rgba(120,120,130,.45);letter-spacing:1px}
.about .ghost{top:385px}

/* services */
.services{top:1804px;height:1007px;background:var(--dark);color:#fff}
.services .tag{left:113px;top:76px;background:#2b2c30}
.services .h2{left:113px;top:108px;color:#fff;width:500px}
.services .intro{left:673px;top:115px;width:414px;font-size:10.5px;line-height:1.6;color:#ddd}
.services .machine{left:84px;top:255px;width:449px;height:658px;background:linear-gradient(180deg,#545b60,#7c8489 45%,#3c4246);}
.svc{position:absolute;left:569px;width:518px;height:163px;border-bottom:1px solid #444}
.svc .ic{position:absolute;left:22px;top:0}
.svc h3{position:absolute;left:22px;top:68px;font-size:17px;font-weight:600}
.svc p{position:absolute;left:22px;top:96px;width:390px;font-size:9.5px;line-height:1.5;color:#cfcfd4}
.services .btn{left:569px;top:896px;width:179px;height:42px}

/* testimonials */
.testi{top:2811px;height:727px;background:var(--grey-bg)}
.testi .tag{left:540px;top:75px}
.testi .h2{left:0;width:1200px;text-align:center;top:110px}
.testi .lead{left:350px;width:500px;text-align:center;top:186px}
.testi .blue{left:88px;top:230px;width:225px;height:188px;background:var(--blue)}
.testi .box{left:113px;top:253px;width:974px;height:343px;background:#fff;box-shadow:0 8px 30px rgba(0,0,0,.06)}
.testi .quote{left:160px;top:323px;width:560px;font-size:10.5px;line-height:1.65;color:#555}
.testi .who{left:160px;top:510px;font-size:14px;font-weight:600;color:var(--ink)}
.testi .role{left:160px;top:532px;font-size:10px;color:var(--blue)}
.testi .photo{left:773px;top:266px;width:301px;height:319px;background:linear-gradient(160deg,#3b6b9a,#88a9c6 50%,#405b78)}
.testi .qmark{left:721px;top:495px;width:105px;height:90px;background:var(--ink);display:flex;align-items:center;justify-content:center}
.testi .pager{left:575px;top:631px;display:flex;gap:6px;align-items:center}
.testi .pager span{width:8px;height:8px;border-radius:50%;background:#b9b9c0}
.testi .pager span:first-child{width:14px;height:14px;background:var(--blue)}
.testi .ghost{top:661px}

/* case studies */
.cases{top:3538px;height:684px;background:#fff}
.cases .tag{left:113px;top:81px}
.cases .h2{left:113px;top:117px;width:520px}
.cases .lead{left:113px;top:197px;width:490px}
.cases .btn{left:907px;top:134px;width:178px;height:40px}
.case{position:absolute;top:248px;width:395px;height:364px;background:#fff;box-shadow:0 6px 22px rgba(0,0,0,.08)}
.case .img{height:226px}
.case h3{font-size:12px;font-weight:600;margin:30px 30px 0;color:var(--ink)}
.case p{font-size:9.5px;line-height:1.5;color:var(--muted);margin:8px 30px 0}
.case .link{display:block;margin:8px 30px 0;font-size:9.5px}

/* contact */
.contact{top:4222px;height:861px;background:#fff}
.contact .map{left:0;top:0;width:1200px;height:585px;background:linear-gradient(135deg,#e2e2e4,#d2d3d6 50%,#e4e4e6)}
.contact .dark{left:905px;top:668px;width:217px;height:193px;background:var(--ink)}
.contact .dark i{position:absolute;left:0;top:0;width:182px;height:193px;background:#fff}
.contact .form{left:113px;top:261px;width:974px;height:571px;background:var(--blue);color:#fff}
.form h2{position:absolute;left:100px;top:60px;font-size:32px;font-weight:600;line-height:1.22}
.form .note{position:absolute;left:577px;top:58px;width:320px;font-size:10.5px;line-height:1.55}
.field{position:absolute;width:388px;border-bottom:1px solid rgba(255,255,255,.7);padding-bottom:10px}
.field label{display:block;font-size:9.5px;font-weight:600}
.field span{display:block;font-size:11px;margin-top:14px}
.form .send{position:absolute;left:100px;top:464px;width:197px;height:40px;background:#fff;color:var(--blue);font-size:9.5px;font-weight:700;display:flex;align-items:center;justify-content:center}

/* footer */
.footer{top:5083px;height:298px;background:#fff;text-align:center}
.footer .logo{left:0;width:1200px;top:10px;display:flex;flex-direction:column;align-items:center;gap:3px;color:var(--ink)}
.footer .logo .dot{width:28px;height:28px;border-radius:50%;background:var(--ink)}
.footer .logo .name{font-size:22px;font-weight:600;letter-spacing:2px}
.footer .logo .sub{font-size:6px;letter-spacing:.6px}
.footer .links{left:0;width:1200px;top:111px;display:flex;justify-content:center;gap:30px;font-size:9.5px;font-weight:600}
.footer .links2{left:0;width:1200px;top:149px;font-size:9px;color:#444;letter-spacing:.4px}
.footer .social{left:528px;top:186px;gap:14px}
.footer .social span{width:24px;height:24px;background:var(--blue);border:none}
.footer .copy{left:0;width:1200px;top:262px;font-size:8.5px;color:#555}
</style>
</head>
<body>

<header class="section topbar">
  <div class="abs crumbs">HELP &nbsp;/&nbsp; SUPPORT &nbsp;/&nbsp; COMMENTS</div>
  <div class="abs follow">Follow Us:</div>
  <div class="social" style="left:990px;top:8px"><span></span><span></span><span></span><span></span></div>
</header>

<nav class="section nav">
  <div class="abs menu"><span>Services</span><span>Industries</span><span>Case Studies</span><span>Process</span><span>About</span></div>
  <div class="abs loc">
    <svg width="12" height="14" viewBox="0 0 12 14"><path d="M6 0a5 5 0 0 0-5 5c0 4 5 9 5 9s5-5 5-9a5 5 0 0 0-5-5zm0 7a2 2 0 1 1 0-4 2 2 0 0 1 0 4z" fill="#2f5cf2"/></svg>
    We're based in South Wales, UK.
  </div>
  <div class="abs phone-ic"><svg width="16" height="16" viewBox="0 0 24 24"><path d="M6.6 10.8a15 15 0 0 0 6.6 6.6l2.2-2.2a1 1 0 0 1 1-.25 11.4 11.4 0 0 0 3.6.57 1 1 0 0 1 1 1V20a1 1 0 0 1-1 1A17 17 0 0 1 3 4a1 1 0 0 1 1-1h3.5a1 1 0 0 1 1 1c0 1.25.2 2.45.57 3.57a1 1 0 0 1-.25 1z" fill="#fff"/></svg></div>
</nav>
<div class="brand"><span class="dot"></span><span class="name">valtorix</span><span class="sub">MECHANICAL DESIGN</span></div>
<div class="call">Get In Touch<b>+44 (0)7700 900 418</b></div>

<section class="section hero">
  <div class="abs photo" role="img" aria-label="Close-up of an engineer's hand sketching mechanical drawings with a pen"></div>
  <div class="abs shade"></div>
  <div class="tag">Mechanical Design Consultancy</div>
  <h1>Precision Mechanical Design for Real-World Products</h1>
  <div class="abs rule"></div>
  <p>Valtorix Design partners with product teams and manufacturers to turn complex mechanical challenges into robust, production-ready solutions.</p>
  <div class="btn">Schedule a Consultation</div>
</section>

<section class="section process">
  <div class="tag">Process</div>
  <h2 class="h2">A Clear Engineering Process from Brief to Build</h2>
  <p class="abs small lead">A structured, transparent process ensures we stay aligned on requirements, risks, and timelines from day one.</p>
  <div class="abs back"></div>
  <div class="abs team" role="img" aria-label="Engineering team reviewing CAD models on computer screens"></div>
  <div class="abs cap"><b><i>1.</i> Free Consultation</b><span>Discuss your project goals and receive expert recommendations.</span></div>
  <div class="abs dots"></div>
  <div class="card" style="left:591px;top:75px;width:229px;height:211px"><div class="num">2.</div><h3>Concept &amp;<br>Feasibility</h3><p>Explore mechanical concepts<br>and architectures</p><span class="link">LEARN MORE</span></div>
  <div class="card" style="left:846px;top:75px;width:241px;height:211px"><div class="num">3.</div><h3>Detailed Design<br>&amp; Simulation</h3><p>3D CAD, assemblies, and<br>mechanisms</p><span class="link">LEARN MORE</span></div>
  <div class="card" style="left:591px;top:313px;width:229px;height:197px"><div class="num">4.</div><h3>Prototype &amp;<br>Refine</h3><p>Support for prototype builds<br>and testing</p><span class="link">LEARN MORE</span></div>
  <div class="card" style="left:846px;top:313px;width:241px;height:197px"><div class="num">5.</div><h3>Handover &amp;<br>Production Support</h3><p>Final drawings, documentation,<br>and BOMs</p><span class="link">LEARN MORE</span></div>
  <div class="btn">Discuss Your Project</div>
</section>

<section class="section about">
  <div class="tag">About Us</div>
  <h2 class="h2">Who We Are</h2>
  <p class="abs small body">Aldric Penhale is the Chief Engineer at Valtorix Design. He has 11 years experience working as a mechanical design engineer in multiple industries including high performance automotive, consumer products, medical, industrial plus many more. He has worked in multiple roles across a wide range of products.</p>
  <div class="btn">More About Us</div>
  <div class="abs mark">valtorix</div>
  <div class="ghost">Valtorix Design</div>
</section>

<section class="section services">
  <div class="tag">Services</div>
  <h2 class="h2">Mechanical Design Services Built for Manufacturing</h2>
  <p class="abs intro">I provide practical, engineering-driven design services that bridge the gap between concept and manufacturable product. Each project is tailored to your technical requirements, budget, and timeline.</p>
  <div class="abs machine" role="img" aria-label="Grey industrial machine enclosure with control panels"></div>

  <div class="svc" style="top:255px">
    <svg class="ic" width="52" height="52" viewBox="0 0 52 52" fill="none" stroke="#2f5cf2" stroke-width="2"><circle cx="22" cy="22" r="8"/><path d="M22 6v5M22 33v5M6 22h5M33 22h5M10.7 10.7l3.5 3.5M29.8 29.8l3.5 3.5M10.7 33.3l3.5-3.5M29.8 14.2l3.5-3.5"/><path d="M34 40l10 10"/></svg>
    <h3>Mechanical Design &amp; Engineering</h3><p>Robust mechanical systems and components designed for real-world use and long-term reliability.</p>
  </div>
  <div class="svc" style="top:418px">
    <svg class="ic" width="52" height="52" viewBox="0 0 52 52" fill="none" stroke="#2f5cf2" stroke-width="2"><path d="M24 4l18 10v20L24 44 6 34V14z"/><circle cx="24" cy="24" r="7"/><path d="M24 17V4M17 28L6 34M31 28l11 6"/></svg>
    <h3>Product Development &amp; Design for Manufacture</h3><p>Helping you move from prototype to scalable production with fewer surprises and lower unit costs.</p>
  </div>
  <div class="svc" style="top:581px">
    <svg class="ic" width="52" height="52" viewBox="0 0 52 52" fill="none" stroke="#2f5cf2" stroke-width="2"><path d="M24 4l20 11v22L24 48 4 37V15z"/><path d="M4 15l20 11 20-11M24 26v22"/><path d="M14 10l20 11"/></svg>
    <h3>CAD, Simulation &amp; Validation</h3><p>Engineering validation to reduce risk before tooling and production investment.</p>
  </div>
  <div class="svc" style="top:744px;border:none">
    <svg class="ic" width="52" height="52" viewBox="0 0 52 52" fill="none" stroke="#2f5cf2" stroke-width="2"><rect x="4" y="8" width="36" height="36"/><path d="M12 36l8-12 6 6 8-14M44 4l4 4-16 16-6 2 2-6z"/></svg>
    <h3>Prototyping Support &amp; Documentation</h3><p>Clear documentation and prototype support to keep your supply chain aligned and efficient.</p>
  </div>
  <div class="btn">Explore All Services</div>
</section>

<section class="section testi">
  <div class="tag">Testimonials</div>
  <h2 class="h2">Feedback from some of our<br>recent customers</h2>
  <p class="abs small lead">Lorem ipsum dolor sit amet, consectetur adipiscing elit, sed do eiusmod tempor incididunt ut labore et dolore magna aliqua.</p>
  <div class="abs blue"></div>
  <div class="abs box"></div>
  <p class="abs quote">I had the pleasure of working alongside Aldric on a day-to-day basis to deliver the most complex machined casting for an 8 speed DCT transmission for an OEM customer.<br>Aldric's support, patience and thorough explanation of the technical challenges through the complex development process allowed me as the Project Manager to confidently manage both the supplier and the customers' expectations daily from an informed and knowledgeable position and made my job so much easier. His flexible and adaptable approach to work, expertise and his ability to work at all levels was a real asset, especially when I was unable to support some supplier and customer meetings, as I could entrust him without worry to pick up the ball and run with it in my absence. A knowledgeable, very good all-rounder that is hard to find these days and is a real pleasure to work with.</p>
  <div class="abs who">Dorian Halsey</div>
  <div class="abs role">Project Manager</div>
  <div class="abs photo" role="img" aria-label="Engineer in a hard hat reviewing notes on a clipboard in a workshop"></div>
  <div class="abs qmark"><svg width="48" height="40" viewBox="0 0 48 40"><path d="M2 2h18v18l-8 18H4l6-16H2zM28 2h18v18l-8 18h-8l6-16h-8z" fill="#fff"/></svg></div>
  <div class="abs pager"><span></span><span></span><span></span></div>
  <div class="ghost">Valtorix Design</div>
</section>

<section class="section cases">
  <div class="tag">Case Studies</div>
  <h2 class="h2">Proven Mechanical Design in Real Projects</h2>
  <p class="abs small lead">Selected projects demonstrating how structured engineering and thoughtful design improve performance, reliability, and manufacturability.</p>
  <div class="btn">View All Projects</div>
  <article class="case" style="left:113px">
    <div class="img" role="img" aria-label="Dark render of a compact engine gearbox assembly" style="background:linear-gradient(135deg,#23272c,#5a6067 50%,#1c1f23)"></div>
    <h3>Compact Mechanism for Portable Device</h3>
    <p>Redesigned a compact mechanical assembly to improve reliability and reduce part count, while keeping tooling and manufacturing costs under control.</p>
    <span class="link">LEARN MORE</span>
  </article>
  <article class="case" style="left:520px">
    <div class="img" role="img" aria-label="Precision metal instrument tip resting on a wooden base against a dark backdrop" style="background:linear-gradient(135deg,#121212,#3a2f24 55%,#7a5a3a)"></div>
    <h3>Compact Mechanism for Portable Device</h3>
    <p>Redesigned a compact mechanical assembly to improve reliability and reduce part count, while keeping tooling and manufacturing costs under control.</p>
    <span class="link">LEARN MORE</span>
  </article>
  <article class="case" style="left:928px">
    <div class="img" role="img" aria-label="Close-up of an automotive transmission assembly" style="background:linear-gradient(135deg,#2a2c30,#6f7379 50%,#3a3d42)"></div>
    <h3>Compact Mechanism for Portable Device</h3>
    <p>Redesigned a compact mechanical assembly to improve reliability and reduce part count, while keeping tooling and manufacturing costs under control.</p>
    <span class="link">LEARN MORE</span>
  </article>
</section>

<section class="section contact">
  <div class="abs map" role="img" aria-label="Muted grey street map of the surrounding region"></div>
  <div class="abs dark"><i></i></div>
  <div class="abs form">
    <h2>Have a Mechanical<br>Design Project in Mind?</h2>
    <p class="note">Share a brief overview of your product, timelines, and any existing CAD or documentation. I'll review and get back to you with next steps.</p>
    <div class="field" style="left:100px;top:138px"><label>First Name</label><span>Lorem Ipsum</span></div>
    <div class="field" style="left:508px;top:138px"><label>Last Name</label><span>Lorem Ipsum</span></div>
    <div class="field" style="left:100px;top:218px"><label>Email</label><span>Lorem Ipsum</span></div>
    <div class="field" style="left:508px;top:218px"><label>Last Name</label><span>Lorem Ipsum</span></div>
    <div class="field" style="left:100px;top:300px;width:796px;height:88px"><label>Message</label><span>Lorem Ipsum</span></div>
    <div class="send">REQUEST A PROJECT CALL</div>
  </div>
</section>

<footer class="section footer">
  <div class="abs logo"><span class="dot"></span><span class="name">valtorix</span><span class="sub">MECHANICAL DESIGN</span></div>
  <div class="abs links"><span>HOME</span><span>WHO WE ARE</span><span>HOW IT WORKS</span><span>WHAT WE OFFER</span><span>CONTACT</span></div>
  <div class="abs links2">HELP &nbsp;&nbsp;/&nbsp;&nbsp; SUPPORT &nbsp;&nbsp;/&nbsp;&nbsp; COMMENTS</div>
  <div class="social"><span></span><span></span><span></span><span></span></div>
  <div class="abs copy">COPYRIGHT © 2025. ALL RIGHTS RESERVED.</div>
</footer>

</body>
</html>
```